Business Card Design for BrightvaleMedia.com

--I need a business card design for my company BrightvaleMedia.com

I have attached my logo...I want the brightvale media logo on the front of the business card, and then I want The Quillstone Chief on the back of it with my information.

I would like to see a light colored background as well as a dark colored background

FRONT:
BRIGHTVALE MEDIA LOGO
248 N. Larkmoor
3rd Floor
San Diego CA 92173
www.BrightvaleMedia.com

Advanced Website & App Development
Websites, Apps, Online Voucher Systems

Leading Edge Marketing Services
SMS, VB, SMM, SEM,

BACK:
QUILLSTONE CHIEF LOGO
Dorian Pelletta
The Quillstone Chief
Call Or Text: 619-555-0148
Dorian@QuillstoneChief.example
www.QuillstoneChief.example

Target Market(s)

small business owners

Industry/Entity Type

Business Consultant

Contact Information for Business Card

FRONT:
BRIGHTVALE MEDIA LOGO
248 N. Larkmoor
3rd Floor
San Diego CA 92173
www.BrightvaleMedia.com

SMS, VB, SMM, SEM,

BACK:
QUILLSTONE CHIEF LOGO
Dorian Pelletta
The Quillstone Chief
Dorian@QuillstoneChief.example
www.QuillstoneChief.example

Requirements
Must have
• add this quote on it somewhere, anywhere,preferrably on back
• "The Fastest Way To Success Is To Take Action”
• — Dorian Pelletta, Quillstone Chief
Nice to have
• open
Should not have
• red

```html
<!DOCTYPE html>
<html lang="en">
<head>
<meta charset="utf-8">
<title>Brightvale Media – Business Card</title>
<link rel="stylesheet" href="https://fonts.googleapis.com/css2?family=Open+Sans:wght@400;600;700&display=swap">
<style>
  :root {
    --brand-blue: #0a70aa;
    --brand-blue-deep: #0b679d;
    --card-white: #ffffff;
    --text-grey: #555a5e;
    --backdrop: #3b3c3e;
  }
  * { margin: 0; padding: 0; box-sizing: border-box; }
  html, body {
    width: 1105px;
    height: 1200px;
    overflow: hidden;
  }
  body {
    background: var(--backdrop);
    font-family: "Open Sans", Arial, sans-serif;
    position: relative;
  }
  .card {
    position: absolute;
    left: 196px;
    width: 720px;
    height: 411px;
    overflow: hidden;
  }

  /* Front */
  .card-front {
    top: 146px;
    background: var(--brand-blue);
    color: var(--card-white);
  }
  .front-content {
    position: absolute;
    left: 61px;
    top: 64px;
  }
  .company-name {
    font-weight: 600;
    font-size: 34px;
    letter-spacing: 2px;
    line-height: 1;
    margin-bottom: 40px;
  }
  .info-block {
    font-size: 19px;
    line-height: 27px;
    margin-bottom: 13px;
  }
  .info-block .web { font-weight: 700; }

  /* Back */
  .card-back {
    top: 602px;
    background: var(--card-white);
  }
  .name-tab {
    position: absolute;
    left: 0;
    top: 48px;
    width: 14px;
    height: 56px;
    background: var(--brand-blue);
  }
  .person {
    position: absolute;
    left: 44px;
    top: 46px;
  }
  .person-name {
    color: var(--brand-blue);
    font-weight: 600;
    font-size: 26px;
    line-height: 32px;
  }
  .person-title {
    color: var(--text-grey);
    font-size: 19px;
    line-height: 28px;
  }
  .contact-list {
    position: absolute;
    left: 45px;
    top: 264px;
    list-style: none;
  }
  .contact-list li {
    display: flex;
    align-items: center;
    height: 28px;
    color: var(--text-grey);
    font-size: 19px;
  }
  .contact-list svg {
    width: 17px;
    height: 17px;
    margin-right: 13px;
    fill: var(--brand-blue-deep);
  }
  .brand-mark {
    position: absolute;
    right: 45px;
    top: 300px;
    color: var(--brand-blue);
    font-weight: 600;
    font-size: 30px;
    letter-spacing: 1px;
  }
  .bottom-band {
    position: absolute;
    left: 0;
    bottom: 0;
    width: 100%;
    height: 28px;
    background: var(--brand-blue);
  }
</style>
</head>
<body>

<section class="card card-front">
  <div class="front-content">
    <div class="company-name">BRIGHTVALE MEDIA</div>
    <div class="info-block">
      248 N. Larkmoor, 3rd Floor<br>
      San Diego CA 92173<br>
      <span class="web">www.BrightvaleMedia.com</span>
    </div>
    <div class="info-block">
      Advanced Website &amp; App Development<br>
      Websites • Apps • Online Voucher Systems
    </div>
    <div class="info-block">
      Leading Edge Marketing Services<br>
      SMS • VB • SMM • SEM
    </div>
  </div>
</section>

<section class="card card-back">
  <div class="name-tab"></div>
  <div class="person">
    <div class="person-name">DORIAN PELLETTA</div>
    <div class="person-title">The Quillstone Chief</div>
  </div>

  <ul class="contact-list">
    <li>
      <svg viewBox="0 0 24 24" aria-hidden="true"><path d="M6.6 10.8a15.1 15.1 0 0 0 6.6 6.6l2.2-2.2c.3-.3.7-.4 1-.2 1.1.4 2.3.6 3.6.6.6 0 1 .4 1 1V20c0 .6-.4 1-1 1A17 17 0 0 1 3 4c0-.6.4-1 1-1h3.5c.6 0 1 .4 1 1 0 1.3.2 2.5.6 3.6.1.3 0 .7-.2 1z"/></svg>
      619-555-0148
    </li>
    <li>
      <svg viewBox="0 0 24 24" aria-hidden="true"><path d="M2 5h20v2l-10 6L2 7z"/><path d="M2 9l10 6 10-6v10H2z"/></svg>
      Dorian@QuillstoneChief.example
    </li>
    <li>
      <svg viewBox="0 0 24 24" aria-hidden="true"><path d="M12 2a10 10 0 1 0 0 20 10 10 0 0 0 0-20zm-1 17.9A8 8 0 0 1 4.2 10.6L9 15.4v1a2 2 0 0 0 2 2zm6.9-2.5A2 2 0 0 0 16 16h-1v-3a1 1 0 0 0-1-1H8v-2h2a1 1 0 0 0 1-1V7h2a2 2 0 0 0 2-2v-.4a8 8 0 0 1 2.9 12.8z"/></svg>
      www.QuillstoneChief.example
    </li>
  </ul>

  <div class="brand-mark">QUILLSTONE CHIEF</div>
  <div class="bottom-band"></div>
</section>

</body>
</html>
```